Site for entrepreneurs/small businesses needs Logo, Homepage

Looking for a logo, either an icon, or stylized text, or a combination of both, and a home page design which fits with it. The logo will be for use on the public website as well as for printed collateral (business cards, post cards, brochures and various other marketing materials).

The site is called Orbitwell (Orbitwell.example). This is to be a national, and eventually an international brand. The new service will provide an easy-to-use platform for entrepreneurs to build their business and web presence together in an integrated way which allows them to focus on their core competency.

The site/service will be dead-simple to use, A/B/C, 1/2/3. We will want some sort of "Get started for FREE" promotional space to collect the person's email address with multiple points of interest which guide the user back to this one call to action: sign up for free. We will feature editorial/blog stories, customer testimonials, and present several key features the the reader just can't live without if they are starting a new business.

Criteria:
* Refer to our comparable sites/logos in the design document attached
* Incorporate our color scheme (but complementary colors welcome)
* No Serif fonts!
* No photo-realistic elements for logo
* Logo must present well in gray scale and/or black/white (for printed materials)
* Strokes/borders that are wider to promote simplicity (vs. thin/precise lines which promote technical complexity)

Inspirations:
* Creative/Custom (but legible) fonts
* Excitement, energetic, jumping for joy
* Karate / Ninja / Power / Precision
* Dance Moves
* Regional influences: California, Silicon Valley, West Coast, Surf City, Beaches, Sunset
* Simple/easy, no-brainer solutions

Target Market(s)

Small Businesses / Entrepreneurs

Logo Text

Orbitwell or Orbitwell.example

Number of Pages Required

1 page

Font styles to use
Sans Serif
Decorative

Requirements
Must have
• See the attached style guide (PDF)

```html
<!DOCTYPE html>
<html lang="en">
<head>
<meta charset="utf-8">
<title>Orbitwell — Build Your Business</title>
<link href="https://fonts.googleapis.com/css2?family=Poppins:wght@300;400;500;600;700&family=Open+Sans:wght@400;600&display=swap" rel="stylesheet">
<style>
:root{
  --navy:#0b2a5b;
  --navy-deep:#061c43;
  --orange:#ef5a2c;
  --orange-light:#f47b3b;
  --ink:#1d1d1d;
  --body:#555;
  --grey-bg:#f3f3f3;
  --white:#fff;
  --black:#0a0a0a;
  --teal:#1f7fa3;
}
*{box-sizing:border-box;margin:0;padding:0}
html,body{width:1200px;height:3974px;overflow:hidden}
body{position:relative;background:var(--white);font-family:'Open Sans',Arial,sans-serif;color:var(--body)}
.abs{position:absolute}
h1,h2,h3,.brand,.nav a{font-family:'Poppins',Arial,sans-serif}

/* header / hero */
.hero-bg{left:0;top:0;width:1200px;height:640px}
.brand{font-weight:700;font-size:40px;color:var(--white);letter-spacing:-0.5px}
.header-brand{left:90px;top:42px}
.phone{left:832px;top:32px;color:var(--white);font-family:'Poppins',sans-serif;font-size:19px;display:flex;align-items:center;gap:8px}
.login{left:1024px;top:27px;width:88px;height:36px;border:2px solid var(--white);border-radius:18px;color:var(--white);font:500 16px 'Poppins',sans-serif;display:flex;align-items:center;justify-content:center}
.nav{left:494px;top:80px;display:flex;gap:0}
.nav a{color:var(--white);text-decoration:none;font-size:16px;margin-right:47px}
.hero-title{left:88px;top:236px;color:var(--white);font-weight:500;font-size:47px;line-height:1.2;white-space:nowrap}
.hero-sub{left:90px;top:306px;color:var(--white);font:400 23px 'Poppins',sans-serif;white-space:nowrap}
.hero-btn{left:90px;top:366px;width:184px;height:42px;background:#fde9dc;border-radius:21px;color:var(--ink);font:400 17px 'Poppins',sans-serif;display:flex;align-items:center;justify-content:center}
.hero-arrows{left:96px;top:458px;display:flex;gap:10px}
.hero-arrows span{width:20px;height:20px;border-radius:50%;background:rgba(255,255,255,.9);display:flex;align-items:center;justify-content:center}
.hero-art{left:650px;top:205px;width:440px;height:500px;border-radius:40px;background:linear-gradient(160deg,#cfe1f5,#6fa0d6 60%,#1f4f94)}

/* signup */
.signup{left:90px;top:697px;width:334px;height:315px;background:var(--orange-light)}
.signup-head{height:71px;background:#e9411f;color:var(--white);font:400 27px 'Poppins',sans-serif;display:flex;align-items:center;justify-content:center}
.signup form{padding:34px 32px 0}
.field{height:46px;background:var(--white);border-radius:3px;margin-bottom:17px;font-size:13px;color:var(--ink);display:flex;align-items:center;padding-left:14px}
.signup-btn{height:48px;background:var(--navy);border-radius:3px;color:var(--white);font-size:17px;display:flex;align-items:center;justify-content:center;margin-top:4px}

.about-title{left:468px;top:790px;font-weight:400;font-size:37px;color:var(--ink)}
.accent{color:var(--orange)}
.about-text{left:466px;top:848px;width:608px;font-size:14.5px;line-height:24px;text-align:justify}

/* features */
.features{left:0;top:1120px;width:1200px;height:620px;background:var(--grey-bg)}
.section-title{width:1200px;left:0;text-align:center;font-weight:400;font-size:36px;color:var(--ink)}
.feature{width:316px;height:316px;text-align:center;padding-top:36px}
.feature.raised{background:var(--white);box-shadow:0 4px 18px rgba(0,0,0,.12)}
.feature-icon{width:96px;height:96px;border-radius:50%;background:var(--orange);margin:0 auto;display:flex;align-items:center;justify-content:center}
.feature h3{font-weight:500;font-size:21px;color:var(--ink);margin:22px 0 18px}
.feature p{font-size:14.5px;line-height:23px;width:240px;margin:0 auto}

/* what we do */
.what-title{left:92px;top:1906px;font-weight:400;font-size:40px;color:var(--ink)}
.what-text{left:94px;top:1970px;width:498px;font-size:14.5px;line-height:24px;text-align:justify}
.what-list{left:94px;top:2065px;list-style:none;font-size:14.5px;line-height:33px}
.what-list li{display:flex;align-items:center;gap:10px}
.what-list li::before{content:"";width:14px;height:14px;border-radius:50%;background:var(--orange);box-shadow:inset 0 0 0 3px var(--orange),inset 0 0 0 5px #fff}
.what-art{left:640px;top:1860px;width:462px;height:445px;border-radius:30px;background:linear-gradient(150deg,#f6f6f6,#e2e2e2 55%,#c9c9c9)}

/* testimonials */
.test-bg{left:0;top:2410px;width:1200px;height:610px;background:radial-gradient(ellipse at center,#eeeeee 0%,#f6f6f6 55%,#fff 80%)}
.quote-mark{left:570px;top:2490px}
.test-title{top:2553px}
.test-text{left:200px;top:2640px;width:800px;text-align:center;font-size:14.5px;line-height:25px}
.avatar{left:558px;top:2745px;width:84px;height:84px;border-radius:50%;background:var(--orange)}
.avatar-inner{left:564px;top:2751px;width:72px;height:72px;border-radius:50%;background:#c94630}
.test-name{left:0;width:1200px;top:2846px;text-align:center;font-size:14px;color:var(--navy)}
.arrow-btn{width:66px;height:66px;border-radius:50%;background:var(--white);box-shadow:0 2px 12px rgba(0,0,0,.12);display:flex;align-items:center;justify-content:center}

/* blog */
.blog-title{top:3090px}
.blog-img{top:3187px;height:363px;background:linear-gradient(160deg,#2b8db4,#1d6f92)}
.blog-card{left:434px;top:3187px;width:324px;height:363px;border:3px solid var(--teal);background:var(--white);padding:50px 30px 0}
.blog-date{font-size:14px;color:var(--ink)}
.blog-card h3{font-weight:400;font-size:24px;line-height:32px;color:var(--ink);margin:20px 0 22px}
.blog-card p{font-size:13px;line-height:22px}
.blog-more{font-size:13px;color:var(--ink);margin-top:26px}

/* footer */
.footer-bg{left:0;top:3620px;width:1200px;height:354px}
.footer-brand{left:90px;top:3784px}
.newsletter-label{left:612px;top:3804px;color:var(--white);font:500 17px 'Poppins',sans-serif}
.newsletter{left:826px;top:3787px;width:282px;height:54px;border:2px solid var(--white);border-radius:27px;color:var(--white);font-size:13px;display:flex;align-items:center;justify-content:space-between;padding:0 18px 0 26px}
.footer-rule{left:90px;top:3872px;width:1020px;height:1px;background:#4a4a4a}
.footer-nav{left:90px;top:3906px;display:flex;gap:30px}
.footer-nav a{color:var(--white);font-size:14px;text-decoration:none}
.copyright{left:866px;top:3908px;color:var(--white);font-size:13px}
</style>
</head>
<body>

<!-- header & hero -->
<svg class="abs hero-bg" viewBox="0 0 1200 640" aria-hidden="true">
  <defs>
    <linearGradient id="heroGrad" x1="0" y1="0" x2="1" y2="1">
      <stop offset="0" stop-color="#0d3370"/>
      <stop offset="1" stop-color="#061c43"/>
    </linearGradient>
  </defs>
  <path d="M0 0H1200V360Q1060 470 820 560Q520 620 0 540Z" fill="url(#heroGrad)"/>
  <path d="M760 580Q1000 500 1200 360V400Q1040 520 840 590Z" fill="#0a0a0a"/>
</svg>
<div class="abs brand header-brand">Orbitwell</div>
<div class="abs phone">
  <svg width="16" height="16" viewBox="0 0 24 24"><path fill="#fff" d="M6.6 10.8a15 15 0 0 0 6.6 6.6l2.2-2.2a1 1 0 0 1 1-.25 11.4 11.4 0 0 0 3.6.6 1 1 0 0 1 1 1V20a1 1 0 0 1-1 1A17 17 0 0 1 3 4a1 1 0 0 1 1-1h3.5a1 1 0 0 1 1 1c0 1.25.2 2.45.6 3.6a1 1 0 0 1-.25 1z"/></svg>
  555-010-4477
</div>
<div class="abs login">Login</div>
<nav class="abs nav"><a>Home</a><a>About us</a><a>Services</a><a>Projects</a><a>Blog</a><a>Contact</a></nav>
<h1 class="abs hero-title">Build Your Business</h1>
<div class="abs hero-sub">Neque porro quisquam est qui dolorem</div>
<div class="abs hero-btn">Get Started Now</div>
<div class="abs hero-arrows">
  <span><svg width="10" height="10" viewBox="0 0 10 10"><path d="M6.5 1.5L3 5l3.5 3.5" stroke="#111" stroke-width="2" fill="none"/></svg></span>
  <span><svg width="10" height="10" viewBox="0 0 10 10"><path d="M3.5 1.5L7 5 3.5 8.5" stroke="#111" stroke-width="2" fill="none"/></svg></span>
</div>
<div class="abs hero-art" role="img" aria-label="Isometric illustration of business people working around a large laptop with charts and icons"></div>

<!-- signup + about -->
<div class="abs signup">
  <div class="signup-head">Get started for FREE</div>
  <form>
    <div class="field">Email address</div>
    <div class="field">Password</div>
    <div class="signup-btn">Sign up for free</div>
  </form>
</div>
<h2 class="abs about-title">About <span class="accent">Orbitwell</span></h2>
<p class="abs about-text">It is a long established fact that a reader will be distracted by the readable content of a page when looking at its layout. The point of using Lorem Ipsum is that it has a more-or-less normal distribution of letters, as opposed to using 'Content here, content here', making it look like readable English. Many desktop publishing packages and web page editors now use Lorem Ipsum as their default model text, and a search for 'lorem ipsum' will uncover many web sites still in their infancy.</p>

<!-- features -->
<section class="abs features"></section>
<h2 class="abs section-title" style="top:1206px">Key Features</h2>
<div class="abs feature" style="left:90px;top:1332px">
  <div class="feature-icon"><svg width="48" height="48" viewBox="0 0 48 48" fill="none" stroke="#fff" stroke-width="2.5"><path d="M24 10a10 10 0 0 0-6 18v5h12v-5a10 10 0 0 0-6-18z"/><path d="M19 38h10M21 42h6M24 2v4M8 10l3 3M40 10l-3 3M4 24h4M40 24h4"/></svg></div>
  <h3>Business</h3>
  <p>The point of using Lorem Ipsum is that it has a more-or-less normal distribution of letters,</p>
</div>
<div class="abs feature raised" style="left:440px;top:1332px">
  <div class="feature-icon"><svg width="48" height="48" viewBox="0 0 48 48" fill="none" stroke="#fff" stroke-width="2.5"><rect x="7" y="10" width="34" height="22" rx="2"/><path d="M20 38h8M24 32v6M14 25l6-6 5 4 8-8"/></svg></div>
  <h3>Software product</h3>
  <p>The point of using Lorem Ipsum is that it has a more-or-less normal distribution of letters,</p>
</div>
<div class="abs feature" style="left:790px;top:1332px">
  <div class="feature-icon"><svg width="48" height="48" viewBox="0 0 48 48" fill="none" stroke="#fff" stroke-width="2.5"><rect x="7" y="9" width="34" height="30" rx="2"/><path d="M7 16h34M12 22h10v11H12zM27 23h9M27 28h9M27 33h6"/></svg></div>
  <h3>Software development</h3>
  <p>The point of using Lorem Ipsum is that it has a more-or-less normal distribution of letters,</p>
</div>

<!-- what we do -->
<h2 class="abs what-title">What we do</h2>
<p class="abs what-text">It is a long established fact that a reader will be distracted by the readable content of a page when looking at its layout. The point of using Lorem Ipsum is that it has a more-or-less normal distribution</p>
<ul class="abs what-list">
  <li>Lorem ipsum dolor sit amet, consectetur adipiscing elit.</li>
  <li>Sed vel dui vel diam ultricies dignissim.</li>
  <li>Mauris eget ante congue egestas at ac mi</li>
  <li>Aliquam pretium quam rhoncus lectus porta euismod.</li>
  <li>Vestibulum non lacus a massa vestibulum mattis.</li>
</ul>
<div class="abs what-art" role="img" aria-label="Isometric illustration of two business people beside an archery target"></div>

<!-- testimonials -->
<div class="abs test-bg" role="img" aria-label="Faint dotted world map background"></div>
<svg class="abs quote-mark" width="60" height="40" viewBox="0 0 60 40"><path fill="#0b2a5b" d="M4 40V22Q4 6 20 2l2 5Q12 11 12 20h10v20zM34 40V22Q34 6 50 2l2 5Q42 11 42 20h10v20z"/></svg>
<h2 class="abs section-title test-title">Customer <span class="accent">Testimonials</span></h2>
<p class="abs test-text"><span class="accent">"</span> It is a long established fact that a reader will be distracted by the readable content of a page when looking at its layout. The point of using Lorem Ipsum is that it has a more-or-less normal distribution of letters, as opposed to using 'Content here, content here', making it look like readable English. Many desktop publishing<span class="accent">"</span></p>
<div class="abs avatar"></div>
<div class="abs avatar-inner" role="img" aria-label="Customer portrait"></div>
<div class="abs test-name">-porro quisquam</div>
<div class="abs arrow-btn" style="left:56px;top:2637px"><svg width="14" height="20" viewBox="0 0 14 20"><path d="M10 3L3 10l7 7" stroke="#444" stroke-width="1.6" fill="none"/></svg></div>
<div class="abs arrow-btn" style="left:1074px;top:2637px"><svg width="14" height="20" viewBox="0 0 14 20"><path d="M4 3l7 7-7 7" stroke="#444" stroke-width="1.6" fill="none"/></svg></div>

<!-- blog -->
<h2 class="abs section-title blog-title">Latest <span class="accent">Blog</span></h2>
<div class="abs blog-img" style="left:90px;width:326px" role="img" aria-label="Illustration of a businessman surrounded by business icons"></div>
<article class="abs blog-card">
  <div class="blog-date">May 12, 2018</div>
  <h3>Porro quisquam est dolorem ipsum</h3>
  <p>The point of using Lorem Ipsum is that it has a more-or-less normal distribution of letters, as opposed to using 'Content here, content here', making it look like readable</p>
  <div class="blog-more">Continue ›</div>
</article>
<div class="abs blog-img" style="left:779px;width:326px" role="img" aria-label="Illustration of people climbing stacked books toward a lightbulb"></div>

<!-- footer -->
<svg class="abs footer-bg" viewBox="0 0 1200 354" aria-hidden="true">
  <path d="M0 0Q600 110 1200 0V354H0Z" fill="#0a0a0a"/>
</svg>
<div class="abs brand footer-brand">Orbitwell</div>
<div class="abs newsletter-label">JOIN OUR NEWSLETTER</div>
<div class="abs newsletter">Email address
  <svg width="20" height="20" viewBox="0 0 20 20"><circle cx="10" cy="10" r="9" fill="#fff"/><path d="M5 10l9-4-3 9-2-3z" fill="#0a0a0a"/></svg>
</div>
<div class="abs footer-rule"></div>
<nav class="abs footer-nav"><a>Home</a><a>About us</a><a>Services</a><a>Projects</a><a>Blog</a><a>Contact</a></nav>
<div class="abs copyright">Copyright © 2018. All Rights Reserved</div>

</body>
</html>
```